Business card for my new company (Accounting firm)

I need a business card for my new business Brightwell Advisory and Ledger SA. Our services are accounting, tax, audit and financial management. Our customers are small companies, start-ups and new companies. The final design has to show financial security, trust and growth. Please find our logo attached to the business card. Text for the business card: Brightwell Advisory and Ledger SA Tomas Varenholt Director and Founder Certified Accountant Tel. 022 418 57 34 tv@clairevalconseil.ch www.clairevalconseil.ch Rue des Vergières 27 1201 Geneva
Target Market(s)
Our customers are small companies, start-ups and new companies.
Industry/Entity Type
Finance And Accounting
Contact Information for Business Card
Claireval Conseil et Comptes SA
Tomas Varenholt
Directeur et Fondateur
Expert-comptable diplômé
Tél. 022 418 57 34
tv@clairevalconseil.ch
www.clairevalconseil.ch
Rue des Vergières 27
1201 Genève

```html
<!DOCTYPE html>
<html lang="fr">
<head>
<meta charset="utf-8">
<title>Claireval Conseil et Comptes SA – Carte de visite</title>
<link href="https://fonts.googleapis.com/css2?family=Roboto:wght@400;500;700&display=swap" rel="stylesheet">
<style>
  :root {
    --brand-blue: #1a6396;
    --accent-blue: #2eaee0;
    --pale-blue: #e6f2fa;
    --ink: #33363a;
    --white: #ffffff;
    --backdrop: #2a2a2c;
  }
  * { margin: 0; padding: 0; box-sizing: border-box; }
  html, body { width: 1200px; height: 960px; overflow: hidden; }
  body {
    background: var(--backdrop);
    font-family: "Roboto", Arial, sans-serif;
    position: relative;
  }
  .card {
    position: absolute;
    left: 220px;
    width: 760px;
    height: 434px;
    overflow: hidden;
    border-radius: 4px;
  }
  .card--back { top: 30px; background: var(--brand-blue); }
  .card--front { top: 496px; background: var(--white); }

  .back-identity {
    position: absolute;
    right: 150px;
    top: 96px;
    text-align: left;
    color: var(--white);
  }
  .brand-name {
    font-weight: 700;
    font-size: 54px;
    letter-spacing: 3px;
    line-height: 1;
  }
  .back-url {
    margin-top: 14px;
    font-size: 17px;
    letter-spacing: 2.5px;
  }

  .front-shapes { position: absolute; inset: 0; }

  .holder {
    position: absolute;
    left: 42px;
    top: 112px;
    color: var(--white);
  }
  .holder-name { font-size: 27px; font-weight: 700; margin-bottom: 6px; }
  .holder-role { font-size: 18px; line-height: 1.3; }

  .contact {
    position: absolute;
    left: 42px;
    top: 250px;
    color: var(--white);
    font-size: 18px;
    line-height: 1.35;
  }
  .address { margin-bottom: 10px; }
  .contact-list { list-style: none; }
  .contact-list li { display: flex; align-items: center; gap: 10px; }
  .contact-list svg { width: 16px; height: 16px; flex: none; }

  .front-identity {
    position: absolute;
    left: 470px;
    width: 290px;
    top: 190px;
    text-align: center;
    color: var(--ink);
  }
  .front-identity .brand-name { font-size: 46px; letter-spacing: 2px; }
</style>
</head>
<body>

  <section class="card card--back" aria-label="Verso de la carte">
    <div class="back-identity">
      <div class="brand-name">CLAIREVAL</div>
      <div class="back-url">www.clairevalconseil.ch</div>
    </div>
  </section>

  <section class="card card--front" aria-label="Recto de la carte">
    <svg class="front-shapes" viewBox="0 0 760 434" width="760" height="434" aria-hidden="true">
      <polygon points="462,0 500,0 430,434 392,434" fill="var(--pale-blue)"/>
      <polygon points="0,0 435,0 365,434 0,434" fill="var(--brand-blue)"/>
      <polygon points="435,0 462,0 392,434 365,434" fill="var(--accent-blue)"/>
    </svg>

    <div class="holder">
      <div class="holder-name">Tomas Varenholt</div>
      <div class="holder-role">Directeur et Fondateur</div>
      <div class="holder-role">Expert-comptable diplômé</div>
    </div>

    <div class="contact">
      <div class="address">Rue des Vergières 27<br>1201 Genève</div>
      <ul class="contact-list">
        <li>
          <svg viewBox="0 0 16 16" aria-hidden="true"><path fill="#fff" d="M3.6 1.5l2.2 2.6-1.3 1.7c.9 2 2.4 3.5 4.4 4.4l1.7-1.3 2.6 2.2-1.2 2.3C6.9 13.5 2.5 9.1 1.3 3.9z"/></svg>
          022 418 57 34
        </li>
        <li>
          <svg viewBox="0 0 16 16" aria-hidden="true"><rect x="1" y="3.5" width="14" height="9.5" fill="#fff"/><path d="M1.5 4l6.5 5 6.5-5" fill="none" stroke="var(--brand-blue)" stroke-width="1.3"/></svg>
          tv@clairevalconseil.ch
        </li>
        <li>
          <svg viewBox="0 0 16 16" aria-hidden="true"><circle cx="8" cy="8" r="7" fill="#fff"/><path d="M1 8h14M8 1c-3 3-3 11 0 14M8 1c3 3 3 11 0 14" fill="none" stroke="var(--brand-blue)" stroke-width="1"/></svg>
          www.clairevalconseil.ch
        </li>
      </ul>
    </div>

    <div class="front-identity">
      <div class="brand-name">CLAIREVAL</div>
    </div>
  </section>

</body>
</html>
```